Design logo, business cards, and web page for new web and bi development consulting company

I've started a Web and Business Intelligence development consulting company. We develop on Quordex's stack, Visual Sudio and Tabula Server. We develop responsive web sites and business intelligence platforms. I plan on focusing on small to medium sized business as my client base. I need a logo, business cards, and a one page web site. We will do more with the web site with you in the next six months if the business survives. The name of the company is Corvalo Integration Solutions, Corvalo for short.

Target Market(s)

small to medium sized businesses

Industry/Entity Type

Business

Contact Information for Business Card

logo
name
title
email
phone

Logo Text

Corvalo Integration Solutions - web and data solutions

Coding

Coded - Design and coding required

Number of Pages Required

1 page

Font styles to use
Sans Serif

Colors
0355a3
0092cd
00a88f
6b449b

Requirements
Nice to have
• web and data solutions

```html
<!DOCTYPE html>
<html lang="en">
<head>
<meta charset="utf-8">
<title>Corvalo — Web and Business Intelligence Development</title>
<link rel="stylesheet" href="https://fonts.googleapis.com/css2?family=Ubuntu:wght@400;500;700&family=Open+Sans:ital,wght@0,400;0,600;0,700;1,400&family=Josefin+Sans:wght@400&display=swap">
<style>
:root{
  --brand:#0d4a9e;
  --nav-top:#1f6fd1;
  --nav-bottom:#0d4fb0;
  --ink:#1a1a1a;
  --text:#444;
  --line:#d6d6d6;
  --button:#111;
  --footer:#252525;
  --footer-text:#7b7b7b;
  --social:#3a3a3a;
}
*{margin:0;padding:0;box-sizing:border-box}
html,body{width:794px;height:1200px;overflow:hidden;background:#fff}
body{position:relative;font-family:"Open Sans",sans-serif;color:var(--text)}
.page{position:relative;width:794px;height:1200px;border-top:2px solid var(--brand)}

.header{position:absolute;top:0;left:0;width:794px;height:56px}
.brand{position:absolute;left:39px;top:10px;display:flex;align-items:center;gap:10px}
.brand-mark{width:34px;height:34px;border-radius:50%;background:var(--brand)}
.brand-name{font-family:"Ubuntu",sans-serif;font-weight:700;font-size:21px;color:var(--brand)}
.phone{position:absolute;right:38px;top:12px;display:flex;align-items:center;gap:10px;font-family:"Ubuntu",sans-serif;font-weight:500;font-size:17px;color:var(--ink)}

.nav{position:absolute;top:56px;left:0;width:794px;height:39px;background:linear-gradient(var(--nav-top),var(--nav-bottom))}
.nav a{position:absolute;top:14px;font-family:"Josefin Sans",sans-serif;font-size:10.5px;color:#fff;text-decoration:none;white-space:nowrap}

.hero{position:absolute;top:95px;left:0;width:794px;height:344px;background:linear-gradient(180deg,#7f8388 0%,#c9cbce 35%,#d4d5d6 60%,#8e9196 100%)}
.hero-photo{position:absolute;inset:0;background:radial-gradient(circle at 570px 150px,#3a6f9a 0,#244866 55px,rgba(255,255,255,.5) 95px,rgba(255,255,255,0) 140px),linear-gradient(90deg,rgba(40,40,45,.55) 0,rgba(40,40,45,0) 90px)}
.hero-panel{position:absolute;left:38px;top:80px;width:292px;height:193px;background:rgba(255,255,255,.86);padding:15px 16px}
.hero-title{font-weight:700;font-size:24px;color:var(--ink);line-height:1.1;white-space:nowrap}
.hero-sub{font-family:"Josefin Sans",sans-serif;font-size:14px;color:var(--ink);line-height:22px;margin-top:8px;white-space:nowrap}
.hero-copy{font-size:8.4px;line-height:15px;color:#555;margin-top:6px;margin-left:2px;white-space:nowrap}
.btn-primary{display:inline-flex;margin-top:11px;margin-left:2px;width:71px;height:28px;background:var(--brand);border-radius:2px;color:#fff;font-size:10px;font-weight:600;align-items:center;justify-content:center}
.dots{position:absolute;top:322px;left:371px;display:flex;gap:7px}
.dots span{width:9px;height:9px;border-radius:50%;background:#e6e6e6}
.dots .active{background:var(--brand)}
.hero-shadow{position:absolute;top:439px;left:110px;width:570px;height:22px;background:radial-gradient(ellipse at 50% 0,rgba(0,0,0,.22),rgba(0,0,0,0) 70%)}

.service{position:absolute;top:476px;width:224px;height:280px;border:1px solid var(--line);background:#fff;padding:10px 10px}
.service::after{content:"";position:absolute;left:20px;right:20px;bottom:-20px;height:18px;background:radial-gradient(ellipse at 50% 0,rgba(0,0,0,.2),rgba(0,0,0,0) 70%)}
.service-kicker{font-family:"Ubuntu",sans-serif;font-weight:400;font-size:14px;color:var(--ink)}
.service-title{font-family:"Ubuntu",sans-serif;font-weight:700;font-size:15px;color:var(--brand);margin-top:1px}
.service-image{width:198px;height:125px;margin-top:11px;margin-left:2px;border:1px solid #ccc}
.service-copy{font-size:8.6px;line-height:14.5px;color:#555;margin-top:14px}
.btn-dark{display:inline-flex;align-items:center;justify-content:center;height:19px;padding:0 7px;background:var(--button);color:#fff;font-size:8.4px;border-radius:2px}
.service .btn-dark{margin-top:10px}

.divider{position:absolute;top:796px;left:38px;width:718px;height:1px;background:#e2e2e2}

.col-title small{display:block;font-family:"Ubuntu",sans-serif;font-weight:700;font-size:14px;color:var(--ink)}
.col-title strong{display:block;font-family:"Ubuntu",sans-serif;font-weight:700;font-size:23px;color:var(--brand);line-height:1.05}
.col-lede{font-style:italic;font-size:10.5px;color:var(--ink);margin-top:7px}
.welcome{position:absolute;left:40px;top:823px;width:330px}
.welcome p{font-size:8.6px;line-height:14.6px;color:#444;margin-top:14px}
.welcome p + p{margin-top:17px}
.welcome .btn-dark{margin-top:13px;height:23px;padding:0 9px}
.video{position:absolute;left:408px;top:823px;width:346px}
.video .col-lede{margin-left:3px}
.player{position:absolute;left:3px;top:71px;width:343px;height:192px;background:radial-gradient(circle at 190px 80px,#6b6058 0,#3a3532 70px,#1d1d1d 170px)}
.player-tools{position:absolute;right:6px;top:7px;display:flex;flex-direction:column;gap:5px}
.player-tools span{width:26px;height:20px;background:rgba(20,20,20,.85);border-radius:2px;color:#fff;font-size:5px;display:flex;flex-direction:column;align-items:center;justify-content:flex-end;padding-bottom:2px}
.player-bar{position:absolute;left:6px;bottom:6px;right:6px;height:22px;background:rgba(20,20,20,.85);border-radius:2px}
.play{position:absolute;left:0;top:0;width:40px;height:22px;background:#111;border-radius:2px}
.track{position:absolute;left:52px;top:10px;width:208px;height:5px;background:#555}
.track i{display:block;width:60px;height:5px;background:#c21818}
.hd{position:absolute;right:18px;top:5px;font-size:9px;font-weight:700;font-style:italic;color:#f0c000}

.footer{position:absolute;left:0;top:1129px;width:794px;height:71px;background:var(--footer)}
.footer-links{position:absolute;left:40px;top:21px;font-size:8.6px;color:var(--footer-text);word-spacing:2px}
.footer-copy{position:absolute;left:40px;top:40px;font-size:8.6px;color:var(--footer-text)}
.social{position:absolute;right:42px;top:21px;display:flex;gap:3px}
.social span{width:24px;height:24px;background:var(--social);border-radius:2px}
</style>
</head>
<body>
<div class="page">

  <header class="header">
    <div class="brand">
      <span class="brand-mark"></span>
      <span class="brand-name">Corvalo</span>
    </div>
    <div class="phone">
      <svg width="32" height="32" viewBox="0 0 32 32" aria-hidden="true">
        <circle cx="16" cy="16" r="14.5" fill="none" stroke="#999" stroke-width="2"/>
        <path d="M12 9c-1.5 1-2 2.6-1.3 5 1 3.3 3.4 6.5 6.3 8.4 1.8 1.1 3.4 1.3 4.6.2l-2.3-3.1-2 .8c-1.6-1-3-3-3.6-4.8l1.6-1.3z" fill="#999"/>
      </svg>
      <span>Call us: 1(800) 555-0147</span>
    </div>
  </header>

  <nav class="nav">
    <a style="left:38px">HOME</a>
    <a style="left:101px">ABOUT »</a>
    <a style="left:171px">SERVICES</a>
    <a style="left:247px">PROJECTS »</a>
    <a style="left:334px">BLOG</a>
    <a style="left:394px">CONTACTS</a>
  </nav>

  <section class="hero">
    <div class="hero-photo" role="img" aria-label="Business hand holding a magnifying glass over a glowing globe linked to people icons, city skyline below"></div>
    <div class="hero-panel">
      <h1 class="hero-title">WEB AND BUSINESS</h1>
      <p class="hero-sub">INTELLIGENCE DEVELOPMENT<br>CONSULTING COMPANY</p>
      <p class="hero-copy">We develop on Quordex's stack, Vantix Sudio and Tabula Server.<br>We also develop responsive web sites...</p>
      <span class="btn-primary">READ MORE</span>
    </div>
    <div class="dots"><span></span><span class="active"></span><span></span></div>
  </section>
  <div class="hero-shadow"></div>

  <article class="service" style="left:39px">
    <p class="service-kicker">Quordex's</p>
    <h2 class="service-title">Stack Development</h2>
    <div class="service-image" role="img" aria-label="Businessman sketching a cloud network diagram" style="background:linear-gradient(135deg,#6f747a,#2b3550 60%,#1b2440)"></div>
    <p class="service-copy">Lorem ipsum dolor sit amet, consectetur adipiscing elit, sed do eiusmod tempor incididunt ut labore et dolore magna aliqua.</p>
    <span class="btn-dark">Read More</span>
  </article>

  <article class="service" style="left:285px">
    <p class="service-kicker">Vantix</p>
    <h2 class="service-title">Studio Development</h2>
    <div class="service-image" role="img" aria-label="Glowing teal data tunnel of code" style="background:radial-gradient(circle at 50% 50%,#e8ffff 0,#5fb6b4 18%,#1e4a4e 55%,#0b1a1d 100%)"></div>
    <p class="service-copy">Lorem ipsum dolor sit amet, consectetur adipiscing elit, sed do eiusmod tempor incididunt ut labore et dolore magna aliqua.</p>
    <span class="btn-dark">Read More</span>
  </article>

  <article class="service" style="left:529px">
    <p class="service-kicker">Tabula</p>
    <h2 class="service-title">Server Development</h2>
    <div class="service-image" role="img" aria-label="Hand drawing a database architecture sketch on glass" style="background:linear-gradient(135deg,#3c3c3c,#6a6a6a 45%,#2c2c2c)"></div>
    <p class="service-copy">Lorem ipsum dolor sit amet, consectetur adipiscing elit, sed do eiusmod tempor incididunt ut labore et dolore magna aliqua.</p>
    <span class="btn-dark">Read More</span>
  </article>

  <div class="divider"></div>

  <section class="welcome">
    <h2 class="col-title"><small>Welcome to</small><strong>Corvalo Development</strong></h2>
    <p class="col-lede">Simply Innovative Business Management</p>
    <p>Neque porro quisquam est, qui dolorem ipsum quia dolor sit amet, consectetur, adipisci velit, sed quia non numquam eius modi tempora incidunt ut labore et dolore magnam aliquam quaerat voluptatem.</p>
    <p>At vero eos et accusamus et iusto odio dignissimos ducimus qui blanditiis prae-sentium voluptatum deleniti atque corrupti quos dolores et quas molestias excep-turi sint occaecati cupiditate non provident, similique sunt in culpa qui officia deserunt mollitia animi, id est laborum et dolorum fuga. Et harum quidem rerum facilis est et expedita distinctio. Nam libero tempore, cum soluta nobis est eligendi optio cumque nihil impedit...</p>
    <span class="btn-dark">Read More</span>
  </section>

  <section class="video">
    <h2 class="col-title"><small>Our</small><strong>Video</strong></h2>
    <p class="col-lede">Explaining our services</p>
    <div class="player">
      <div style="position:absolute;inset:0" role="img" aria-label="Video frame of a consultant writing a web strategy mind map on glass"></div>
      <div class="player-tools">
        <span>LIKE</span><span>LATER</span><span>SHARE</span><span>EMBED</span>
      </div>
      <div class="player-bar">
        <span class="play"><svg width="40" height="22" viewBox="0 0 40 22" aria-hidden="true"><path d="M17 6l8 5-8 5z" fill="#fff"/></svg></span>
        <span class="track"><i></i></span>
        <span class="hd">HD</span>
      </div>
    </div>
  </section>

  <footer class="footer">
    <p class="footer-links">Home &nbsp;/&nbsp; About us &nbsp;/&nbsp; Services &nbsp;/&nbsp; Projects &nbsp;/&nbsp; Blog &nbsp;/&nbsp; Contacts</p>
    <p class="footer-copy">©2015 Corvalo. All rights reserved.</p>
    <div class="social"><span></span><span></span><span></span><span></span><span></span></div>
  </footer>

</div>
</body>
</html>
```